Brainwave state designs for neurofeedback report

Design ORIGINAL graphics that correspond with existing colors and shapes for Halo Prism Grid of Stillness & Halo Prism Rhythm Panel for "Normal", "Bright Harbor", "Summit Tide" etc... patterns. You can change the shape of the white outline to be more modern looking. Perhaps you can also use white background with black outline. The frequency bars (can be more ordered) but keep the general shape of the outline.

• An original flair. Modern. Neurotechish
• Do not copy the design. Add your original ideas. Choose a font that complements the design.

```html
<!DOCTYPE html>
<html lang="en">
<head>
<meta charset="utf-8">
<title>The Halo Prism – Grid of Stillness</title>
<link rel="stylesheet" href="https://fonts.googleapis.com/css2?family=Poppins:wght@300;500;600;800&display=swap">
<style>
  :root {
    --ink: #1f2226;
    --muted: #8a8f98;
    --grid: #d3d6dc;
    --paper: #ffffff;
    --beta: #f26330;
    --beta-deep: #e0502a;
    --amber: #fbb334;
    --lemon: #f0e446;
    --alpha: #174d27;
    --theta: #8497cd;
    --delta: #8b5aa8;
    --beta-tint: #fdebe2;
    --alpha-tint: #e2ece5;
    --theta-tint: #e9edf8;
    --delta-tint: #f0e7f5;
    --sky-top: #4fb4e6;
    --sky-low: #b6e0f6;
    --sea-top: #1276c0;
    --sea-deep: #262b66;
  }
  html, body {
    margin: 0;
    padding: 0;
    width: 1200px;
    height: 848px;
    overflow: hidden;
    background: var(--paper);
  }
  .canvas {
    display: block;
    width: 1200px;
    height: 848px;
    font-family: "Poppins", sans-serif;
  }
  .title-light { font-weight: 300; font-size: 50px; fill: var(--ink); }
  .title-bold { font-weight: 800; font-size: 50px; fill: var(--ink); }
  .band-label { font-weight: 600; font-size: 13px; fill: var(--ink); }
  .freq-label { font-weight: 600; font-size: 11px; fill: var(--ink); text-anchor: middle; }
  .axis-label { font-weight: 500; font-size: 11px; fill: var(--muted); text-anchor: middle; }
  .axis-line { stroke: var(--ink); stroke-width: 1.4; }
  .grid-line { stroke: var(--grid); stroke-width: 1; stroke-dasharray: 3 4; }
  .halo-outline { fill: rgba(255,255,255,0.72); stroke: var(--ink); stroke-width: 1.6; stroke-linejoin: round; }
  .bar-beta { fill: var(--beta); }
  .bar-beta-deep { fill: var(--beta-deep); }
  .bar-amber { fill: var(--amber); }
  .bar-lemon { fill: var(--lemon); }
  .bar-alpha { fill: var(--alpha); }
  .bar-theta { fill: var(--theta); }
  .bar-delta { fill: var(--delta); }
</style>
</head>
<body>
<svg class="canvas" viewBox="0 0 1200 848" xmlns="http://www.w3.org/2000/svg">
  <defs>
    <linearGradient id="iceberg-scene" x1="0" x2="0" y1="0" y2="1">
      <stop offset="0" stop-color="var(--sky-top)"/>
      <stop offset="0.47" stop-color="var(--sky-low)"/>
      <stop offset="0.475" stop-color="var(--sea-top)"/>
      <stop offset="1" stop-color="var(--sea-deep)"/>
    </linearGradient>
  </defs>

  <g class="heading">
    <text class="title-light" x="93" y="160">THE HALO PRISM</text>
    <text class="title-bold" x="93" y="222">GRID OF STILLNESS</text>
  </g>

  <!-- State bands -->
  <g class="bands">
    <rect x="95" y="344" width="625" height="144" rx="6" fill="var(--beta-tint)"/>
    <rect x="95" y="488" width="625" height="72" fill="var(--alpha-tint)"/>
    <rect x="95" y="560" width="625" height="72" fill="var(--theta-tint)"/>
    <rect x="95" y="632" width="625" height="72" rx="6" fill="var(--delta-tint)"/>
    <rect x="95" y="344" width="4" height="144" fill="var(--beta)"/>
    <rect x="95" y="488" width="4" height="72" fill="var(--alpha)"/>
    <rect x="95" y="560" width="4" height="72" fill="var(--theta)"/>
    <rect x="95" y="632" width="4" height="72" fill="var(--delta)"/>
  </g>

  <g class="band-labels">
    <rect x="114" y="366" width="8" height="8" rx="2" fill="var(--beta)"/>
    <text class="band-label" x="130" y="375">Beta</text>
    <text class="band-label" x="130" y="392">Concious</text>
    <text class="band-label" x="130" y="409">Mind</text>
    <rect x="114" y="510" width="8" height="8" rx="2" fill="var(--alpha)"/>
    <text class="band-label" x="130" y="519">Alpha</text>
    <text class="band-label" x="130" y="536">Bridge</text>
    <rect x="114" y="574" width="8" height="8" rx="2" fill="var(--theta)"/>
    <text class="band-label" x="130" y="583">Theta</text>
    <text class="band-label" x="130" y="600">Subconcious</text>
    <text class="band-label" x="130" y="617">Mind</text>
    <rect x="114" y="646" width="8" height="8" rx="2" fill="var(--delta)"/>
    <text class="band-label" x="130" y="655">Delta</text>
    <text class="band-label" x="130" y="672">unconcious</text>
    <text class="band-label" x="130" y="689">Mind</text>
  </g>

  <!-- Amplitude grid -->
  <g class="grid">
    <line class="grid-line" x1="401" y1="344" x2="401" y2="704"/>
    <line class="grid-line" x1="344" y1="344" x2="344" y2="704"/>
    <line class="grid-line" x1="287" y1="344" x2="287" y2="704"/>
    <line class="grid-line" x1="555" y1="344" x2="555" y2="704"/>
    <line class="grid-line" x1="612" y1="344" x2="612" y2="704"/>
    <line class="grid-line" x1="669" y1="344" x2="669" y2="704"/>
  </g>

  <!-- Halo envelope -->
  <path class="halo-outline" d="M395 340 L395 380 L408 404 L389 428 L380 452 L372 476 L372 500 L306 524 L321 548 L380 572 L366 596 L385 620 L323 644 L336 668 L414 692 L414 708 L546 708 L546 692 L578 668 L590 644 L574 620 L593 596 L557 572 L704 548 L704 524 L597 500 L588 476 L576 452 L569 428 L554 404 L582 380 L582 340 Z"/>

  <!-- Frequency bars -->
  <g class="bars">
    <rect class="bar-beta" x="403" y="349" width="55" height="14" rx="7"/><rect class="bar-beta" x="498" y="349" width="76" height="14" rx="7"/>
    <rect class="bar-beta" x="403" y="373" width="55" height="14" rx="7"/><rect class="bar-beta" x="498" y="373" width="76" height="14" rx="7"/>
    <rect class="bar-beta-deep" x="416" y="397" width="42" height="14" rx="7"/><rect class="bar-beta-deep" x="498" y="397" width="48" height="14" rx="7"/>
    <rect class="bar-beta" x="397" y="421" width="61" height="14" rx="7"/><rect class="bar-beta" x="498" y="421" width="63" height="14" rx="7"/>
    <rect class="bar-amber" x="388" y="445" width="70" height="14" rx="7"/><rect class="bar-amber" x="498" y="445" width="70" height="14" rx="7"/>
    <rect class="bar-lemon" x="380" y="469" width="78" height="14" rx="7"/><rect class="bar-lemon" x="498" y="469" width="82" height="14" rx="7"/>
    <rect class="bar-alpha" x="380" y="493" width="78" height="14" rx="7"/><rect class="bar-alpha" x="498" y="493" width="91" height="14" rx="7"/>
    <rect class="bar-alpha" x="314" y="517" width="144" height="14" rx="7"/><rect class="bar-alpha" x="498" y="517" width="198" height="14" rx="7"/>
    <rect class="bar-alpha" x="329" y="541" width="129" height="14" rx="7"/><rect class="bar-alpha" x="498" y="541" width="198" height="14" rx="7"/>
    <rect class="bar-theta" x="388" y="565" width="70" height="14" rx="7"/><rect class="bar-theta" x="498" y="565" width="51" height="14" rx="7"/>
    <rect class="bar-theta" x="374" y="589" width="84" height="14" rx="7"/><rect class="bar-theta" x="498" y="589" width="87" height="14" rx="7"/>
    <rect class="bar-theta" x="393" y="613" width="65" height="14" rx="7"/><rect class="bar-theta" x="498" y="613" width="68" height="14" rx="7"/>
    <rect class="bar-delta" x="331" y="637" width="127" height="14" rx="7"/><rect class="bar-delta" x="498" y="637" width="84" height="14" rx="7"/>
    <rect class="bar-delta" x="344" y="661" width="114" height="14" rx="7"/><rect class="bar-delta" x="498" y="661" width="72" height="14" rx="7"/>
    <rect class="bar-delta" x="422" y="685" width="36" height="14" rx="7"/><rect class="bar-delta" x="498" y="685" width="40" height="14" rx="7"/>
  </g>

  <!-- Frequency scale (Hz) -->
  <g class="freq-scale">
    <text class="freq-label" x="478" y="360">40</text>
    <text class="freq-label" x="478" y="384">38</text>
    <text class="freq-label" x="478" y="408">30</text>
    <text class="freq-label" x="478" y="432">24</text>
    <text class="freq-label" x="478" y="456">19</text>
    <text class="freq-label" x="478" y="480">15</text>
    <text class="freq-label" x="478" y="504">12.5</text>
    <text class="freq-label" x="478" y="528">10.5</text>
    <text class="freq-label" x="478" y="552">9</text>
    <text class="freq-label" x="478" y="576">7.5</text>
    <text class="freq-label" x="478" y="600">6</text>
    <text class="freq-label" x="478" y="624">4</text>
    <text class="freq-label" x="478" y="648">3</text>
    <text class="freq-label" x="478" y="672">1.5</text>
    <text class="freq-label" x="478" y="696">0.75</text>
  </g>

  <!-- Amplitude axes -->
  <g class="axes">
    <line class="axis-line" x1="258" y1="722" x2="458" y2="722"/>
    <line class="axis-line" x1="401" y1="716" x2="401" y2="728"/>
    <line class="axis-line" x1="344" y1="716" x2="344" y2="728"/>
    <line class="axis-line" x1="287" y1="716" x2="287" y2="728"/>
    <line class="axis-line" x1="498" y1="722" x2="710" y2="722"/>
    <line class="axis-line" x1="555" y1="716" x2="555" y2="728"/>
    <line class="axis-line" x1="612" y1="716" x2="612" y2="728"/>
    <line class="axis-line" x1="669" y1="716" x2="669" y2="728"/>
    <text class="axis-label" x="287" y="746">9.0</text>
    <text class="axis-label" x="344" y="746">6.0</text>
    <text class="axis-label" x="401" y="746">3.0</text>
    <text class="axis-label" x="555" y="746">3.0</text>
    <text class="axis-label" x="612" y="746">6.0</text>
    <text class="axis-label" x="669" y="746">9.0</text>
  </g>

  <!-- Iceberg illustration area -->
  <rect class="iceberg-panel" x="742" y="288" width="346" height="443" rx="28" fill="url(#iceberg-scene)" role="img" aria-label="Illustration of an iceberg: a small peak above the waterline and a large mass beneath the sea"/>

  <!-- State key strip -->
  <g class="state-strip">
    <rect x="1096" y="344" width="8" height="142" rx="4" fill="var(--beta)"/>
    <rect x="1096" y="490" width="8" height="68" rx="4" fill="var(--alpha)"/>
    <rect x="1096" y="562" width="8" height="68" rx="4" fill="var(--theta)"/>
    <rect x="1096" y="634" width="8" height="70" rx="4" fill="var(--delta)"/>
  </g>
</svg>
</body>
</html>
```